All-Natural Head Lice Removal company

I need a business card with my pre-existing logo. We are a new company located in Portland Oregon that goes into peoples homes to help with head lice removal. My products and approach are all- natural and also will be around children.On my current logo we used Teal Bl and the color Green. I am open to new ideas just want it simple and creative

Target Market(s)

my biggest market is families of school aged children

Industry/Entity Type

Business

Contact Information for Business Card

see upload for details from previous business card

Font styles to use
Serif

Colors
33a6d7
9bcb3b
f37122

Requirements
Must have
• Basic information/ logo put into a creative format that is catching to the eye
Nice to have
• creative

```html
<!DOCTYPE html>
<html lang="en">
<head>
<meta charset="utf-8">
<title>NitClear Business Card</title>
<link rel="stylesheet" href="https://fonts.googleapis.com/css2?family=Roboto+Slab:wght@400;600;700&display=swap">
<style>
  :root {
    --canvas: #ececea;
    --card: #ffffff;
    --ink-dark: #222325;
    --ink-mid: #5a5c5e;
    --teal-blue: #33a6d7;
    --leaf-green: #6cb43f;
    --logo-green: #9bcb3b;
    --on-dark: #ffffff;
  }
  * { box-sizing: border-box; margin: 0; padding: 0; }
  html, body {
    width: 1200px; height: 913px; overflow: hidden;
    background: var(--canvas);
    font-family: "Roboto Slab", Georgia, serif;
  }
  .canvas {
    position: relative; width: 1200px; height: 913px;
    display: flex; align-items: center; justify-content: center; gap: 50px;
  }
  .card {
    position: relative; width: 525px; height: 300px;
    background: var(--card); border-radius: 16px; overflow: hidden;
    box-shadow: 0 6px 18px rgba(0,0,0,0.18);
  }
  .card-wave { position: absolute; inset: 0; width: 100%; height: 100%; }

  .brand {
    display: flex; align-items: center; gap: 10px;
    color: var(--ink-dark); font-weight: 700;
  }
  .brand-dot { border-radius: 50%; background: var(--logo-green); flex: none; }

  /* front */
  .front .tagline {
    position: absolute; top: 22px; right: 160px;
    font-size: 12px; color: var(--ink-mid); letter-spacing: 0.1px;
    white-space: nowrap;
  }
  .front .brand { position: absolute; left: 34px; top: 118px; font-size: 34px; }
  .front .brand-dot { width: 46px; height: 46px; }
  .contact {
    position: absolute; right: 22px; top: 100px; text-align: right;
    color: var(--on-dark);
  }
  .contact-name { font-size: 15px; font-weight: 600; letter-spacing: 0.3px; white-space: nowrap; }
  .contact-role {
    font-size: 10px; color: var(--teal-blue); letter-spacing: 1px;
    margin: 3px 0 14px;
  }
  .contact-line {
    display: flex; align-items: center; justify-content: flex-end; gap: 7px;
    font-size: 11.5px; line-height: 18px; white-space: nowrap;
  }
  .contact-line svg { width: 10px; height: 10px; fill: none; stroke: var(--teal-blue); stroke-width: 1.6; }

  /* back */
  .back { display: flex; flex-direction: column; align-items: center; justify-content: center; }
  .back .brand { font-size: 46px; margin-bottom: 30px; }
  .back .brand-dot { width: 60px; height: 60px; }
  .back-copy {
    text-align: center; color: var(--ink-dark);
    font-size: 12.5px; font-weight: 600; line-height: 18px;
  }
</style>
</head>
<body>
<main class="canvas">
  <section class="card front" aria-label="Card front">
    <svg class="card-wave" viewBox="0 0 525 300" preserveAspectRatio="none" aria-hidden="true">
      <path fill="var(--leaf-green)" d="M384 0 C344 60 366 150 282 226 C232 268 160 292 94 300 L525 300 L525 0 Z"/>
      <path fill="var(--teal-blue)" d="M392 0 C352 60 374 150 290 226 C240 268 168 292 102 300 L525 300 L525 0 Z"/>
      <path fill="var(--ink-dark)" d="M402 0 C362 60 384 150 300 226 C250 268 178 292 112 300 L525 300 L525 0 Z"/>
    </svg>
    <p class="tagline">All Natural In-Home Lice Removal Services</p>
    <div class="brand"><span class="brand-dot"></span><span class="brand-name">NitClear</span></div>
    <div class="contact">
      <p class="contact-name">DANA WHITFIELD</p>
      <p class="contact-role">OWNER</p>
      <p class="contact-line">1-800-555-0142
        <svg viewBox="0 0 10 10"><path d="M2 1 L4 3 L3 4.5 Q4.5 6.5 5.5 7 L7 6 L9 8 L7.5 9.5 Q3 8.5 0.5 2.5 Z"/></svg></p>
      <p class="contact-line">dana@nitclear.com
        <svg viewBox="0 0 10 10"><rect x="0.8" y="2" width="8.4" height="6"/><path d="M0.8 2 L5 5.5 L9.2 2"/></svg></p>
      <p class="contact-line">www.nitclear.com
        <svg viewBox="0 0 10 10"><circle cx="5" cy="5" r="4"/><path d="M1 5 H9 M5 1 Q2.5 5 5 9 M5 1 Q7.5 5 5 9"/></svg></p>
    </div>
  </section>

  <section class="card back" aria-label="Card back">
    <div class="brand"><span class="brand-dot"></span><span class="brand-name">NitClear</span></div>
    <div class="back-copy">
      <p>Try NitClear Today and Be Lice Free Tomorrow!</p>
      <p>All Natural In-Home Lice Removal Services</p>
      <p>www.nitclear.com</p>
    </div>
  </section>
</main>
</body>
</html>
```